label for wine brand Tierra Velo

we are interested interested in designing a label for a red wine of Spanish origin that is modern, but at the same time classic. The style we are looking for is in line with Chilean wines. Labels of two bodies with colorful, metallic stamping, thinking in Asian markets. We accept labels with watermarks, artistic, original but that are made thinking that the product to sell is wine.

Target Market(s)

United States and Asia

Industry/Entity Type

Commercial

Font styles to use
Decorative
Script

Requirements
Must have
• elegant and modern style
Nice to have
• metal texts
Should not have
• Drawings of animals

```html
<!DOCTYPE html>
<html lang="en">
<head>
<meta charset="utf-8">
<title>Tierra Velo – Pinot Noir Reserva Label</title>
<link rel="stylesheet" href="https://fonts.googleapis.com/css2?family=Josefin+Sans:wght@600&family=Pinyon+Script&display=swap">
<style>
  :root {
    --backdrop: #000000;
    --label-black: #1b1a18;
    --label-edge: #2a2825;
    --gold: #c9a15a;
    --gold-light: #e2c17e;
    --silver: #d9d9d9;
    --art-dark: #232220;
    --art-mid: #4a4946;
  }
  html, body {
    margin: 0;
    padding: 0;
    width: 870px;
    height: 1200px;
    overflow: hidden;
    background: var(--backdrop);
  }
  .canvas {
    position: relative;
    width: 870px;
    height: 1200px;
    background: var(--backdrop);
  }
  .label {
    position: absolute;
    left: 165px;
    top: 193px;
    width: 540px;
    height: 814px;
    background: var(--label-black);
    box-shadow: inset 0 0 0 1px var(--label-edge);
  }
  .label__line {
    position: absolute;
    left: 0;
    right: 0;
    text-align: center;
    transform: translateY(-50%);
    margin: 0;
    line-height: 1;
  }
  .label__origin,
  .label__varietal,
  .label__grade,
  .label__vintage {
    font-family: "Josefin Sans", sans-serif;
    font-weight: 600;
    color: var(--gold);
    background: linear-gradient(180deg, var(--gold-light), var(--gold));
    -webkit-background-clip: text;
    background-clip: text;
    -webkit-text-fill-color: transparent;
  }
  .label__origin   { top: 64px;  font-size: 30px; letter-spacing: 2px; }
  .label__brand {
    top: 222px;
    font-family: "Pinyon Script", cursive;
    font-size: 78px;
    color: var(--silver);
  }
  .label__art {
    position: absolute;
    left: 70px;
    top: 280px;
    width: 400px;
    height: 268px;
  }
  .label__varietal { top: 594px; font-size: 32px; letter-spacing: 1.5px; }
  .label__grade    { top: 680px; font-size: 30px; letter-spacing: 11px; padding-left: 11px; }
  .label__vintage  { top: 746px; font-size: 30px; letter-spacing: 2px; }
</style>
</head>
<body>
  <main class="canvas">
    <section class="label">
      <p class="label__line label__origin">SPAIN</p>
      <h1 class="label__line label__brand">Tierra Velo</h1>
      <svg class="label__art" viewBox="0 0 400 268" role="img" aria-label="Grape cluster above an engraved vineyard estate house">
        <defs>
          <radialGradient id="artGlow" cx="50%" cy="55%" r="60%">
            <stop offset="0%" stop-color="var(--art-mid)"/>
            <stop offset="100%" stop-color="var(--art-dark)" stop-opacity="0"/>
          </radialGradient>
        </defs>
        <rect width="400" height="268" fill="url(#artGlow)"/>
      </svg>
      <p class="label__line label__varietal">PINOT NOIR</p>
      <p class="label__line label__grade">RESERVA</p>
      <p class="label__line label__vintage">2014</p>
    </section>
  </main>
</body>
</html>
```